Postcard Design Project

Company Name - RK Office Essentials LLC We service and Repair printers, Fax and Copiers and sells all Business Technology supplies including supplies for Printers and Copiers to all NYC Metropolitan area.

Target Market(s)

NYC Small to Medium size business

Industry/Entity Type

Business

Font styles to use
Sans Serif

Colors

Designer to choose colors to be used in the design.

Requirements
Must have
• Printer Repairs and Toners Sales

```html
<!DOCTYPE html>
<html lang="en">
<head>
<meta charset="utf-8">
<title>RK Office Essentials – Postcard</title>
<link rel="stylesheet" href="https://fonts.googleapis.com/css2?family=Barlow:wght@600;700;800&family=Lato:wght@400;700;900&display=swap">
<style>
  :root{
    --blue:#1f5fa6;
    --blue-bright:#2a73bf;
    --navy:#1a4f8d;
    --grey:#6d6e71;
    --grey-dark:#3d3e40;
    --yellow:#fdd02f;
    --white:#ffffff;
    --page:#e6e7e9;
    --photo-a:#c9ced4;
    --photo-b:#5b6168;
  }
  *{margin:0;padding:0;box-sizing:border-box}
  html,body{width:971px;height:1200px;overflow:hidden;background:var(--page)}
  .canvas{position:relative;width:971px;height:1200px}
  .card{position:absolute;left:81px;width:809px;height:540px;background:var(--white);overflow:hidden;box-shadow:0 3px 10px rgba(0,0,0,.25)}
  .card--front{top:53px}
  .card--back{top:607px}
  .shapes{position:absolute;inset:0}
  .txt{position:absolute;white-space:nowrap}

  /* front */
  .headline{left:29px;top:42px;font:800 81px/0.95 "Barlow",sans-serif;color:var(--blue);letter-spacing:-0.5px}
  .promo{left:29px;top:233px;font:700 18.5px/1.6 "Lato",sans-serif;color:var(--white)}
  .call-label{left:29px;top:320px;font:700 20px "Lato",sans-serif;color:var(--grey)}
  .call-number{left:27px;top:345px;font:900 45px "Lato",sans-serif;color:var(--grey)}
  .web-label{left:29px;top:440px;font:400 20px "Lato",sans-serif;color:var(--white)}
  .web-url{left:29px;top:466px;font:700 31px "Lato",sans-serif;color:var(--white)}
  .badge-name{left:382px;top:248px;font:700 17px "Lato",sans-serif;color:var(--grey-dark);transform:rotate(9deg);transform-origin:left top;display:flex;align-items:center;gap:6px}
  .badge-name i{display:inline-block;width:14px;height:14px;background:var(--blue)}
  .badge-cta{left:366px;top:322px;font:800 20px/1.15 "Barlow",sans-serif;color:var(--white);text-align:center;transform:rotate(9deg);transform-origin:center}

  /* back */
  .back-promo{left:31px;top:220px;font:800 27px/1.1 "Barlow",sans-serif;color:var(--navy)}
  .back-call-label{left:31px;top:345px;font:700 23px "Barlow",sans-serif;color:var(--white)}
  .back-call-number{left:29px;top:363px;font:800 62px "Barlow",sans-serif;color:var(--white)}
  .back-web{left:0;width:809px;top:475px;text-align:center;font:800 32px "Barlow",sans-serif;color:var(--white)}
  .back-brand{left:471px;top:225px;font:700 25px "Lato",sans-serif;color:var(--grey-dark);display:flex;align-items:center;gap:10px}
  .back-brand i{display:inline-block;width:24px;height:24px;background:var(--blue)}
</style>
</head>
<body>
<main class="canvas">

  <section class="card card--front" aria-label="Postcard front">
    <svg class="shapes" viewBox="0 0 809 540" width="809" height="540">
      <defs>
        <linearGradient id="photoTone" x1="0" y1="0" x2="1" y2="1">
          <stop offset="0" stop-color="var(--photo-a)"/>
          <stop offset="1" stop-color="var(--photo-b)"/>
        </linearGradient>
      </defs>
      <polygon points="549,0 567,0 479,202 461,202" fill="var(--blue)"/>
      <polygon points="567,0 809,0 809,202 479,202" fill="url(#photoTone)" role="img" aria-label="Photo: gloved hand servicing a printer print head"/>
      <rect x="470" y="202" width="339" height="17" fill="var(--blue)"/>
      <polygon points="470,219 488,219 396,540 378,540" fill="var(--blue)"/>
      <polygon points="488,219 809,219 809,540 396,540" fill="url(#photoTone)" role="img" aria-label="Photo: hands replacing a toner cartridge in an office printer"/>
      <polygon points="0,226 391,226 391,301 0,301" fill="var(--blue)"/>
      <polygon points="0,425 391,425 363,540 0,540" fill="var(--grey)"/>
      <circle cx="462" cy="321" r="120" fill="var(--grey)"/>
      <circle cx="462" cy="321" r="110" fill="var(--white)"/>
      <path d="M354,302 L571,336 A110,110 0 0 1 354,302 Z" fill="var(--blue)"/>
    </svg>
    <h1 class="txt headline">GOT DIRTY<br>PRINTER?</h1>
    <p class="txt promo">Also check out our unbeatable<br>Ink and Toner online prices</p>
    <p class="txt call-label">CALL TODAY:</p>
    <p class="txt call-number">718-555-0142</p>
    <p class="txt web-label">Visit us. Online</p>
    <p class="txt web-url">www.rkessentials.com</p>
    <p class="txt badge-name"><i></i>RK Office Essentials</p>
    <p class="txt badge-cta">GET A TECHNICIAN<br>IN YOUR OFFICE<br>TODAY</p>
  </section>

  <section class="card card--back" aria-label="Postcard back">
    <svg class="shapes" viewBox="0 0 809 540" width="809" height="540">
      <defs>
        <linearGradient id="photoToneBack" x1="0" y1="0" x2="1" y2="1">
          <stop offset="0" stop-color="var(--photo-a)"/>
          <stop offset="1" stop-color="var(--photo-b)"/>
        </linearGradient>
      </defs>
      <polygon points="0,0 278,0 470,454 0,454" fill="var(--grey)"/>
      <polygon points="0,0 268,0 355,206 0,206" fill="url(#photoToneBack)" role="img" aria-label="Photo: hands changing colour toner cartridges in a printer"/>
      <polygon points="0,206 355,206 404,321 0,321" fill="var(--yellow)"/>
      <polygon points="0,321 404,321 460,454 0,454" fill="var(--blue)"/>
      <rect x="0" y="454" width="809" height="5" fill="var(--yellow)"/>
      <rect x="0" y="459" width="809" height="81" fill="var(--blue-bright)"/>
      <rect x="674" y="45" width="90" height="90" fill="var(--grey-dark)"/>
      <g stroke="var(--grey-dark)" stroke-width="1">
        <line x1="466" y1="350" x2="764" y2="350"/>
        <line x1="466" y1="395" x2="764" y2="395"/>
        <line x1="466" y1="440" x2="764" y2="440"/>
      </g>
    </svg>
    <p class="txt back-promo">ALSO CHECK OUT OUR<br>UNBEATABLE INK AND<br>TONER ONLINE PRICES</p>
    <p class="txt back-call-label">CALL TODAY:</p>
    <p class="txt back-call-number">718-555-0142</p>
    <p class="txt back-brand"><i></i>RK Office Essentials</p>
    <p class="txt back-web">VISIT US. ONLINE : WWW.RKESSENTIALS.COM</p>
  </section>

</main>
</body>
</html>
```